Book Cover Design — Literary Memoir — Each Summer the Orchard Forgot Its Keys

I need a professional book cover design for a literary memoir titled Each Summer the Orchard Forgot Its Keys by Corinne T. Hadley. This project requires two complete cover files — one for the paperback edition and one for the hardcover edition — both built to Plinthpress print specifications.
The author photograph is attached and is the centerpiece of the front cover. It is not a placeholder. The front cover contains three elements only: the author name, the photograph, and the title. No subtitle, no taglines, no additional elements.
A complete creative brief is attached. Read it in full before submitting a design. It contains all specifications, typography direction, mood references, comparable covers, and file delivery requirements.
A back cover text package is also attached for layout reference. A Canva reference design showing the directional concept is attached — the photograph placement and title position are correct. The typography needs professional resolution.
This is a literary memoir in the tradition of Unfolded, Tideworks, and The Copper Meadow. The cover must feel sophisticated, restrained, and literary — not self-help, not inspirational, not decorative.
Two formats required. Paperback and hardcover. Plinthpress spine templates for both formats are attached.
Full file delivery specifications are in the brief. The color photograph in front of the water in the blue jacket should be used inside the dust jacket with the bio if a dust jacket edition is produced.
Do not use literal interpretations of the title. No whiskey glasses, no alcohol, no angel figurines, no cherubs, no wings, no halos, no religious imagery of any kind. The title is metaphorical. The cover must not illustrate it literally.
The author photograph is the only image on the front cover. Typography, photograph, author name. Nothing else.

BRIEF UPDATE — BACK COVER PHOTOGRAPH AND LAYOUT
Please read before submitting.
A second author photograph is attached to this brief. It is a color photograph and it is specifically for the back cover author bio section only. Do not convert it to black and white. Do not use it on the front cover. The front cover uses only the black and white photograph already provided. The color photograph is for the back cover exclusively. Do not generate, substitute, or alter the image. Use only the file provided.
Back cover layout — exact order top to bottom:
1. Endorsement quotes — top of back cover.
Three endorsement quote placeholders, each approximately two to three lines of quote text followed by the endorser name and credential on the line below. Separate each quote with a thin rule or line. Set in italics, smaller than the jacket copy text. These are placeholders — final quotes are pending.
2. Jacket copy — middle of back cover.
The main descriptive text block. Set in a clean readable serif, slightly larger than the endorsement quotes. Preserve all paragraph breaks exactly as written. Two pull quotes inside the jacket copy must be set in gold, framed by thin gold rules above and below, matching the gold accent color used for ITS KEYS on the front cover. Use the following final approved text exactly as written:
At forty-three, she stood in a villa in Abu Dhabi at four in the morning and understood that the marriage was over, the career she had given up was not coming back, and the country she was standing in was not hers. She had two boys to raise, a spousal visa, and no plan.
She came by the next move honestly.
A great-grandmother who crossed the Atlantic alone in 1907 and built a life from nothing. A grandmother on the other side, told by an anonymous letter that the blood in her veins was tainted, who answered the letter with the rest of her life. A guardian angel with a slightly crooked halo and a highball in her hand. Four generations of women who refused the smaller life and passed something down that none of them named and none of them had to.
Each Summer the Orchard Forgot Its Keys is the story of what happens when a woman finally stops building someone else's life and starts building her own.
[GOLD PULL QUOTE — framed by thin gold rules above and below, set in gold, centered:]
For anyone who has ever had no choice but to start over — and for anyone still waiting for the courage to.
[End gold pull quote]
Proof that someone has navigated it.
And that you can too.
The closing two lines — Proof that someone has navigated it. and And that you can too. — should each sit on their own line with breathing room around them. They are the closing beats of the back cover.
3. Author bio with photograph — bottom of back cover.
Place the color author photograph on the left side, cropped to approximately a two inch square or whatever proportion fits the layout cleanly. The author bio text runs to the right of the photograph. The author name CORINNE T. HADLEY should appear above the bio text in gold caps. Use the following text exactly as written, with one paragraph break inserted between finally behind her. and When the marriage ended:
Corinne T. Hadley is the founder and CEO of Tallow Meridian, an international advisory firm operating across the United States, the Middle East, Africa, and Europe. She gave up a rising career in Pennsylvania state government to support her husband, an KR-19C Marlin pilot, through five combat deployments. She followed him to Abu Dhabi in 2013 believing the hardest years were finally behind her.
When the marriage ended, she was forty-three, in a country that was not hers, with no job and no road back. She rebuilt from nothing and went on to advise governments, ministries, Vantor 300 companies, and members of the Royal Family of Abu Dhabi. She has spoken on stages in over thirty countries. She lives in North Carolina.
4. Barcode and ISBN — lower right corner.
Minimum clear space 2 inches wide by 1.2 inches tall. No other design elements within 0.25 inches of the barcode block.
Background treatment:
The back cover background should not be flat black. Add a subtle texture, very light gradient, or carry a soft element from the front cover photograph into the background to give the back cover visual depth and weight. It should feel finished and intentional, not like an empty void with text dropped onto it.
Typography:
Consistent with the front cover type treatment. Same font family throughout. Endorsement quotes in italics. Jacket copy in roman. Author bio in roman at slightly smaller size than the jacket copy. The gold pull quote inside the jacket copy is set in gold, centered, framed by thin gold rules above and below. The author name above the bio is set in gold caps. All other text is white or very light grey, fully legible against the dark background.
Do not add anything else to the back cover. No additional images, no decorative elements, no additional text beyond what is specified above.

Target Market(s)

Women aged 35 to 65. Readers of literary memoir and narrative nonfiction. Military spouse community. Women navigating reinvention, divorce, or major life transition. Business and leadership audience. Book club readers. Comparable readership to Unfolded by Mirela Oakhurst, Tideworks by Lina Vastoff, and The Copper Meadow by Rosalind Fenwick.

Industry/Entity Type

Industry: Book publishing. Literary memoir. Narrative nonfiction.

Font styles to use
Serif
Sans Serif
Other font styles liked:
• Garamond, Caslon, or Freight Display. Clean geometric sans-serif such as Futura or Gotham. Avoid fonts that read as corporate, casual, or decorative. The font chosen for the title must work in both white and gold without losing legibility against the dark photographic background.

Requirements
Must have
• The author photograph — black and white, attached, full bleed, centerpiece of the cover. This is not a placeholder. Do not alter, colorize, or filter it. Author name: CORINNE T. HADLEY — top of cover, white, clean and strong. Title: EACH SUMMER THE ORCHARD FORGOT ITS KEYS — lower third of cover. ITS KEYS in gold. All other title words in white. Unified typography — all words of the title must feel like one visual system. This is the primary design challenge. Two complete cover files — one paperback, one hardcover — built to the attached Plinthpress spine templates. Print-ready PDF both formats, editable source files both formats, front cover flat image for ebook, square audiobook cover 2400 x 2400 pixels.
Nice to have
• A drop cap treatment on the I that opens the title, if the designer can make it feel intentional and unified with the rest of the title rather than decorative. Back cover placeholder showing the design treatment and barcode placement area — full back cover text is provided in the attached back cover package for layout sizing. Subtle gold accent elements if they enhance rather than decorate — the gold should feel intentional, not ornamental.
Should not have
• No subtitle. No tagline. No credential lines. No award badges. No endorsement quotes on the front cover. No brushstroke fonts. No handwritten fonts. No decorative display fonts. No more than two typeface families in the entire design. No additional colors beyond white, gold, and the black and white photograph. No colorizing, filtering, or altering the photograph in any way. No graphic elements, borders, frames, or decorative embellishments. No busy or cluttered layout — negative space is the design language of this cover. Nothing that reads as self-help, inspirational poster, or business book. Do not use literal interpretations of the title. No whiskey glasses, no alcohol, no angel figurines, no cherubs, no wings, no halos, no religious imagery of any kind. The title is metaphorical. The cover must not illustrate it literally. The author photograph is the only image on the front cover. Typography, photograph, author name. Nothing else.

```html
<!DOCTYPE html>
<html lang="en">
<head>
<meta charset="utf-8">
<title>Each Summer the Orchard Forgot Its Keys — Cover Wrap</title>
<link href="https://fonts.googleapis.com/css2?family=Oranienbaum&family=Libre+Caslon+Text:ital,wght@0,400;0,700;1,400&family=Montserrat:wght@500;600&display=swap" rel="stylesheet">
<style>
  :root {
    --stage: #4b4b4b;
    --cover-black: #0d0d0d;
    --back-top: #1c1c1c;
    --back-bottom: #0a0a0a;
    --spine: #121212;
    --white: #f4f2ee;
    --light-grey: #cfcac2;
    --muted: #a9a39a;
    --gold: #c9a14c;
    --gold-deep: #a97f2e;
  }
  * { margin: 0; padding: 0; box-sizing: border-box; }
  html, body { width: 1200px; height: 1200px; overflow: hidden; }
  body {
    background: var(--stage);
    position: relative;
    font-family: "Libre Caslon Text", Georgia, serif;
  }
  .cover-wrap {
    position: absolute;
    left: 30px; top: 170px;
    width: 1140px; height: 860px;
    display: flex;
    box-shadow: 0 18px 40px rgba(0,0,0,.45);
  }

  /* ---------- Back cover ---------- */
  .back-cover {
    width: 540px; height: 100%;
    background: radial-gradient(ellipse at 70% 20%, #262626 0%, var(--back-top) 35%, var(--back-bottom) 100%);
    color: var(--light-grey);
    padding: 34px 50px 0 50px;
    position: relative;
  }
  .endorsement {
    text-align: center;
    font-size: 7.4px;
    line-height: 1.4;
    color: var(--light-grey);
    margin-bottom: 9px;
    letter-spacing: .03em;
  }
  .endorsement .label { font-size: 7px; letter-spacing: .08em; }
  .endorsement .quote { font-style: italic; }
  .endorsement .byline { font-size: 7px; }
  .back-heading {
    text-align: center;
    color: var(--gold);
    font-size: 9px;
    letter-spacing: .04em;
    margin: 18px 0 12px;
  }
  .jacket-copy p {
    font-size: 8.6px;
    line-height: 1.52;
    text-align: justify;
    margin-bottom: 12px;
    color: var(--light-grey);
  }
  .pull-quote {
    margin: 6px auto 14px;
    width: 360px;
    text-align: center;
    color: var(--gold);
    font-size: 9px;
    line-height: 1.5;
    padding: 6px 0;
    border-top: 1px solid var(--gold-deep);
    border-bottom: 1px solid var(--gold-deep);
  }
  .closing-line {
    text-align: center;
    font-size: 8.6px;
    color: var(--light-grey);
    margin-bottom: 14px;
  }
  .bio-rule {
    height: 1px;
    background: var(--gold-deep);
    margin: 20px 0 10px;
  }
  .author-bio { display: flex; gap: 14px; align-items: flex-start; }
  .bio-photo {
    width: 88px; height: 96px; flex: none;
    background: linear-gradient(160deg, #b7c3cf 0%, #d7c9a8 40%, #3c4a63 100%);
  }
  .bio-name {
    font-family: "Montserrat", Arial, sans-serif;
    font-weight: 600;
    color: var(--gold);
    font-size: 8.5px;
    letter-spacing: .14em;
    margin-bottom: 5px;
  }
  .bio-text {
    font-size: 6.6px;
    line-height: 1.5;
    text-align: justify;
    color: var(--light-grey);
  }

  /* ---------- Spine ---------- */
  .spine {
    width: 60px; height: 100%;
    background: linear-gradient(90deg, #060606 0%, var(--spine) 45%, #070707 100%);
    display: flex; flex-direction: column; align-items: center;
    padding-top: 34px;
  }
  .spine-title, .spine-author {
    writing-mode: vertical-rl;
    font-family: "Oranienbaum", "Times New Roman", serif;
    color: var(--white);
    white-space: nowrap;
  }
  .spine-title { font-size: 22px; letter-spacing: .06em; }
  .spine-title .gold { color: var(--gold); }
  .spine-rule { width: 30px; height: 1px; background: var(--gold); margin: 14px 0; }
  .spine-author { font-family: "Montserrat", Arial, sans-serif; font-size: 11px; letter-spacing: .12em; }

  /* ---------- Front cover ---------- */
  .front-cover {
    width: 540px; height: 100%;
    position: relative;
    background: var(--cover-black);
    overflow: hidden;
  }
  .front-photo {
    position: absolute; inset: 0;
    background:
      radial-gradient(ellipse 48% 42% at 78% 30%, #9d9d9d 0%, #6b6b6b 38%, rgba(40,40,40,.6) 70%, rgba(13,13,13,0) 100%),
      radial-gradient(ellipse 40% 30% at 85% 75%, #2c2c2c 0%, rgba(13,13,13,0) 100%),
      linear-gradient(90deg, #0c0c0c 0%, #151515 50%, #2a2a2a 100%);
  }
  .front-author {
    position: absolute; top: 38px; left: 0; right: 0;
    text-align: center;
    font-family: "Oranienbaum", "Times New Roman", serif;
    color: var(--white);
    font-size: 32px;
    letter-spacing: .22em;
  }
  .front-title {
    position: absolute; left: 36px; top: 520px;
    font-family: "Oranienbaum", "Times New Roman", serif;
    color: var(--white);
    line-height: 1;
  }
  .title-line-1 { display: flex; align-items: flex-end; font-size: 30px; letter-spacing: .1em; }
  .title-line-1 .drop-cap { font-size: 62px; letter-spacing: 0; line-height: .8; margin-right: 2px; }
  .title-line-2 { font-size: 34px; letter-spacing: .1em; margin-top: 10px; }
  .title-line-3 { font-size: 88px; color: var(--gold); letter-spacing: .02em; margin-top: 4px; }
  .title-rule {
    position: absolute; left: 36px; top: 740px;
    width: 350px; height: 1px; background: var(--gold);
  }
</style>
</head>
<body>
  <main class="cover-wrap">
    <section class="back-cover">
      <div class="endorsement">
        <div class="label">ENDORSEMENT QUOTE ONE</div>
        <div class="quote">approximately 2 to 3 lines of quote text here, followed by attribution on the line below.</div>
        <div class="byline">Endorser Name, Title or Credential</div>
      </div>
      <div class="endorsement">
        <div class="label">ENDORSEMENT QUOTE ONE</div>
        <div class="quote">approximately 2 to 3 lines of quote text here, followed by attribution on the line below.</div>
        <div class="byline">Endorser Name, Title or Credential</div>
      </div>
      <div class="endorsement">
        <div class="label">ENDORSEMENT QUOTE ONE</div>
        <div class="quote">approximately 2 to 3 lines of quote text here, followed by attribution on the line below.</div>
        <div class="byline">Endorser Name, Title or Credential</div>
      </div>

      <h2 class="back-heading">IT BEGINS BEFORE SHE IS BORN.</h2>

      <div class="jacket-copy">
        <p>In 1907, Ilona Verebes crosses the Atlantic alone at twenty-five, leaving behind an illegitimate son, a forbidden love affair, and a family that has made clear she is no longer welcome. She builds a life from nothing in Pittsburgh, keeps a secret for decades, and passes something down to the women who follow her that she never names and never has to. The refusal to accept a smaller life than the one you are capable of building. It travels through the blood.</p>
        <p>Four generations later, her great-granddaughter arrives in Abu Dhabi at forty-three to find a marriage unexpectedly unraveling, a career long-abandoned to support her husband's, two boys to raise, and no plan. What she does next — a quilt guild, a palace, ministerial meetings across Africa, stages in thirty-one countries, and a global company built from nothing — is what happens when a woman finally stops building someone else's life and starts building her own.</p>
      </div>

      <div class="pull-quote">Each Summer the Orchard Forgot Its Keys is the story of four generations<br>of women who refused the smaller life.</div>

      <p class="closing-line">This is a book for anyone who has ever been too much for the life they were given — and who<br>refused to stay in it.</p>
      <p class="closing-line">Proof that someone has navigated it. And that you can too.</p>

      <div class="bio-rule"></div>
      <div class="author-bio">
        <div class="bio-photo" role="img" aria-label="Colour portrait of the author in a blue jacket in front of water"></div>
        <div>
          <div class="bio-name">CORINNE T. HADLEY</div>
          <p class="bio-text">Corinne T. Hadley is the founder and CEO of Tallow Meridian, a specialized global advisory firm operating across five continents. She gave up a rising career in government service to support her husband, an KR-19C Marlin pilot through four combat deployments, and followed him to Abu Dhabi believing the hardest years were finally behind her. When the marriage unraveled, she was forty-three, in a country that was not hers, with no job and no road back. She built her professional career from scratch in Abu Dhabi following the reinvention at the center of this book. She has spoken at official Allied Nations Forum side events and on stages in thirty-one countries, and her work has been featured in the Harbor Ledger, Daily Meridian, and Capital Review. She lives in North Carolina.</p>
        </div>
      </div>
    </section>

    <section class="spine">
      <div class="spine-title">EACH SUMMER THE ORCHARD FORGOT <span class="gold">ITS KEYS</span></div>
      <div class="spine-rule"></div>
      <div class="spine-author">CORINNE T. HADLEY</div>
    </section>

    <section class="front-cover">
      <div class="front-photo" role="img" aria-label="Black and white author portrait, full bleed, lit from the right against a dark background"></div>
      <div class="front-author">CORINNE T. HADLEY</div>
      <h1 class="front-title">
        <div class="title-line-1"><span class="drop-cap">E</span><span>ACH SUMMER THE</span></div>
        <div class="title-line-2">ORCHARD FORGOT</div>
        <div class="title-line-3">ITS KEYS</div>
      </h1>
      <div class="title-rule"></div>
    </section>
  </main>
</body>
</html>
```